Veltrano.co - Polar Expeditions Specialists

We need a modern, visually striking business card for Veltrano.co, a company specialized in selling expedition cruises to the most remote regions on Earth, with a focus on the Arctic and Antarctica. The design should instantly communicate that the cardholder is an expert in polar travel. Use clean, premium aesthetics with cool tones like icy blue and white, possibly incorporating polar imagery (ice, glaciers, penguins, etc.)

Attached the logo

Contact Information for Business Card

Feels high-end and trustworthy.. Visually memorable — encourages people to keep it

Colors
0054AA
0677BA
7BADD7
CADEEF
E8F1F8

Requirements
Must have
• ice, glaciers, penguins, montains
Nice to have
• modern, transparente,

```html
<!DOCTYPE html>
<html lang="en">
<head>
<meta charset="utf-8">
<title>Veltrano.co Business Card</title>
<link href="https://fonts.googleapis.com/css2?family=Poppins:wght@500;800&family=Roboto:wght@400;700&display=swap" rel="stylesheet">
<style>
  :root {
    --card-blue: #3574b5;
    --deep-blue: #0054aa;
    --ice: #e8f1f8;
    --white: #ffffff;
    --backdrop: #3a3a3c;
  }
  * { box-sizing: border-box; margin: 0; padding: 0; }
  html, body { width: 1200px; height: 689px; overflow: hidden; }
  body {
    background: var(--backdrop);
    position: relative;
    font-family: "Roboto", Arial, sans-serif;
    color: var(--white);
  }
  .card {
    position: absolute;
    top: 194px;
    width: 540px;
    height: 300px;
    background: var(--card-blue);
    border-radius: 18px;
    overflow: hidden;
  }
  .card--front { left: 40px; }
  .card--back { left: 620px; }

  .brand {
    display: flex;
    align-items: center;
    gap: 14px;
  }
  .brand__dot {
    width: 46px; height: 46px;
    border-radius: 50%;
    background: var(--white);
    flex: none;
  }
  .brand__name {
    font-family: "Poppins", sans-serif;
    font-weight: 800;
    font-size: 50px;
    line-height: 1;
    letter-spacing: 1px;
  }
  .brand__tagline {
    font-family: "Poppins", sans-serif;
    font-weight: 500;
    font-size: 13.5px;
    letter-spacing: 0.3px;
    margin-top: 4px;
  }
  .card--front .brand-block {
    position: absolute;
    left: 80px; top: 108px;
  }
  .card--front .brand__tagline { margin-left: 60px; }

  .card--back .brand-block {
    position: absolute;
    left: 34px; top: 42px;
  }
  .card--back .brand__name { font-size: 40px; }
  .card--back .brand__tagline { font-size: 11px; }

  .holder {
    position: absolute;
    left: 34px; top: 118px;
  }
  .holder__name {
    font-family: "Poppins", sans-serif;
    font-weight: 800;
    font-size: 17px;
    letter-spacing: 0.5px;
  }
  .holder__title { font-size: 12px; margin-top: 2px; }

  .address {
    position: absolute;
    left: 34px; top: 172px;
    font-size: 13px;
    line-height: 1.35;
    font-style: normal;
  }
  .contacts {
    position: absolute;
    left: 34px; top: 216px;
    list-style: none;
    font-size: 13px;
    line-height: 1.35;
  }
  .contacts li { display: flex; align-items: center; gap: 8px; }
  .contacts svg { width: 11px; height: 11px; flex: none; }

  .polar-illustration {
    position: absolute;
    right: -30px; top: 10px;
    width: 290px; height: 320px;
    border-radius: 48% 40% 30% 52% / 40% 45% 40% 45%;
    background: radial-gradient(circle at 45% 40%, var(--white) 0%, var(--ice) 70%, #cadeef 100%);
  }
</style>
</head>
<body>
  <section class="card card--front">
    <div class="brand-block">
      <div class="brand">
        <span class="brand__dot"></span>
        <span class="brand__name">Veltrano.co</span>
      </div>
      <p class="brand__tagline">Polar Expeditions Specialists</p>
    </div>
  </section>

  <section class="card card--back">
    <div class="polar-illustration" role="img" aria-label="White silhouette of a polar bear with two penguins and small stars"></div>

    <div class="brand-block">
      <div class="brand">
        <span class="brand__name">Veltrano.co</span>
      </div>
      <p class="brand__tagline">Polar Expeditions Specialists</p>
    </div>

    <div class="holder">
      <p class="holder__name">ELIAS MORROW</p>
      <p class="holder__title">President</p>
    </div>

    <address class="address">
      4120 Glacier Row<br>
      Nordhaven, Canada 58213
    </address>

    <ul class="contacts">
      <li>
        <svg viewBox="0 0 12 12" aria-hidden="true"><path fill="#fff" d="M2.5 1l2 2.2-1 1.3a6 6 0 0 0 4 4l1.3-1L11 9.5 9.7 11C5 11 1 7 1 2.3z"/></svg>
        555-210-4187
      </li>
      <li>
        <svg viewBox="0 0 12 12" aria-hidden="true"><rect x="3" y="0.7" width="6" height="10.6" rx="1" fill="none" stroke="#fff" stroke-width="1.2"/><circle cx="6" cy="9.6" r="0.6" fill="#fff"/></svg>
        555-382-9046
      </li>
      <li>
        <svg viewBox="0 0 12 12" aria-hidden="true"><rect x="0.5" y="2" width="11" height="8" fill="#fff"/><path d="M0.5 2.3L6 6.5l5.5-4.2" fill="none" stroke="#3574b5" stroke-width="1"/></svg>
        hello@veltrano.co
      </li>
      <li>
        <svg viewBox="0 0 12 12" aria-hidden="true"><circle cx="6" cy="6" r="5.3" fill="none" stroke="#fff" stroke-width="1.2"/><path d="M0.7 6h10.6M6 0.7c-2.5 3-2.5 7.6 0 10.6M6 0.7c2.5 3 2.5 7.6 0 10.6" fill="none" stroke="#fff" stroke-width="0.9"/></svg>
        www.veltrano.co
      </li>
    </ul>
  </section>
</body>
</html>
```